Moravel Aesthetic Doctor

I require an elegant, luxurious looking business card for my aesthetic business. I am a doctor and that will set me aside from competitors. I am planning to provide home and spa based treatments to clients with high expectations. I have attached my logo.

```html
<!DOCTYPE html>
<html lang="en">
<head>
<meta charset="utf-8">
<title>Moravel Aesthetic Doctor – Business Card</title>
<link href="https://fonts.googleapis.com/css2?family=Marcellus&family=Roboto:wght@300;400;500&display=swap" rel="stylesheet">
<style>
  :root {
    --bg: #2b2c2e;
    --sky: #6cc3ea;
    --sky-light: #bfe6f7;
    --silver: #b9bcbf;
    --grey-text: #9a9da0;
    --ink-soft: #8f9295;
    --white: #ffffff;
  }
  * { box-sizing: border-box; margin: 0; padding: 0; }
  html, body { width: 1200px; height: 904px; overflow: hidden; }
  body {
    background: var(--bg);
    font-family: "Roboto", sans-serif;
    display: flex;
    flex-direction: column;
    align-items: center;
    justify-content: center;
    gap: 40px;
  }
  .card {
    width: 700px;
    height: 400px;
    position: relative;
    overflow: hidden;
    box-shadow: 0 10px 30px rgba(0,0,0,.45);
  }

  /* Front */
  .card--front {
    background: linear-gradient(160deg, var(--sky-light) 0%, #c9d4da 40%, var(--silver) 70%, #a9d8ee 100%);
    display: flex;
    flex-direction: column;
    align-items: center;
    justify-content: center;
  }
  .brand {
    display: flex;
    align-items: center;
    gap: 18px;
  }
  .brand__mark {
    width: 70px; height: 70px;
    border-radius: 50%;
    border: 3px solid currentColor;
    flex: none;
  }
  .brand__name {
    font-family: "Marcellus", serif;
    font-weight: 400;
    text-transform: uppercase;
    letter-spacing: 3px;
    line-height: 1.05;
  }
  .card--front .brand { color: var(--white); }
  .card--front .brand__name { font-size: 40px; }
  .services {
    margin-top: 40px;
    color: var(--white);
    text-align: center;
    font-weight: 300;
    font-size: 18px;
    line-height: 1.5;
    letter-spacing: .3px;
  }

  /* Back */
  .card--back {
    background: var(--white);
    border-bottom: 8px solid var(--sky);
    padding: 48px 56px 0;
  }
  .card--back .brand { color: var(--grey-text); justify-content: center; }
  .card--back .brand__mark { border-color: var(--silver); width: 80px; height: 80px; }
  .card--back .brand__name { font-size: 38px; }
  .details {
    margin-top: 48px;
    display: flex;
    align-items: center;
    justify-content: center;
    gap: 32px;
  }
  .person { text-align: right; }
  .person__name {
    color: var(--sky);
    font-weight: 500;
    font-size: 22px;
  }
  .person__post { font-size: 14px; margin-left: 4px; }
  .person__cred {
    color: var(--ink-soft);
    font-weight: 300;
    font-size: 17px;
    line-height: 1.35;
    margin-top: 4px;
  }
  .divider { width: 1px; height: 96px; background: var(--silver); }
  .contact { list-style: none; }
  .contact li {
    display: flex;
    align-items: center;
    gap: 12px;
    color: var(--ink-soft);
    font-weight: 300;
    font-size: 17px;
    line-height: 1.65;
  }
  .contact svg { width: 16px; height: 16px; flex: none; }
  .contact .accent { color: var(--sky); }
  .social {
    display: flex;
    gap: 14px;
    justify-content: center;
    margin-top: 26px;
    margin-left: 260px;
  }
  .social span {
    width: 24px; height: 24px;
    border-radius: 50%;
    background: var(--sky);
  }
</style>
</head>
<body>

  <section class="card card--front">
    <div class="brand">
      <span class="brand__mark"></span>
      <span class="brand__name">Moravel Aesthetic Doctor</span>
    </div>
    <p class="services">
      Dermal injectables • Plasma facials • Microneedling<br>
      Skin boosters • Excessive sweating<br>
      Home and Spa Based Treatments
    </p>
  </section>

  <section class="card card--back">
    <div class="brand">
      <span class="brand__mark"></span>
      <span class="brand__name">Moravel Aesthetic Doctor</span>
    </div>

    <div class="details">
      <div class="person">
        <p class="person__name">Dr Lena Varga,<span class="person__post">MRCPCH MD</span></p>
        <p class="person__cred">Australasian Diploma<br>of Aesthetic Medicine</p>
      </div>
      <span class="divider"></span>
      <ul class="contact">
        <li>
          <svg viewBox="0 0 16 16" aria-hidden="true"><path d="M3 1.5l2.5 0 1 3.2-1.6 1.2a8 8 0 0 0 5.2 5.2l1.2-1.6 3.2 1v2.5c0 .6-.5 1-1 1C7 14 2 9 2 2.5c0-.5.4-1 1-1z" fill="var(--sky)"/></svg>
          0800 555 014
        </li>
        <li>
          <svg viewBox="0 0 16 16" aria-hidden="true"><rect x="1.5" y="3.5" width="13" height="9" rx="1" fill="none" stroke="var(--sky)" stroke-width="1.4"/><path d="M2 4.5l6 4.5 6-4.5" fill="none" stroke="var(--sky)" stroke-width="1.4"/></svg>
          lena@moravel.co.nz
        </li>
        <li>
          <svg viewBox="0 0 16 16" aria-hidden="true"><circle cx="8" cy="8" r="6.3" fill="none" stroke="var(--sky)" stroke-width="1.3"/><ellipse cx="8" cy="8" rx="2.6" ry="6.3" fill="none" stroke="var(--sky)" stroke-width="1.1"/><path d="M1.8 8h12.4" stroke="var(--sky)" stroke-width="1.1"/></svg>
          <span>www.<span class="accent">moravel</span>.co.nz</span>
        </li>
      </ul>
    </div>

    <div class="social" aria-label="Social media">
      <span></span><span></span>
    </div>
  </section>

</body>
</html>
```